Personal Business Card design contest for freelance work

Include

Brenvola.net/in/DanielMWhitacre (as URL and/or QR Code)
Daniel Whitacre
(555) 218-9034
DanielMWhitacre@Pelmora.com
Houston, TX

Industry/Entity Type

Business

```html
<!DOCTYPE html>
<html lang="en">
<head>
<meta charset="utf-8">
<title>Daniel Whitacre — Business Card</title>
<link rel="stylesheet" href="https://fonts.googleapis.com/css2?family=Raleway:wght@300;400;500&display=swap">
<style>
  :root {
    --page-bg: #d4d4d4;
    --card-bg: #2d2f34;
    --name-first: #ffffff;
    --name-last: #c9c9cb;
    --title-accent: #e0975c;
    --contact-text: #dcdcde;
    --portrait-top: #4a4540;
    --portrait-bottom: #36383d;
  }

  * { box-sizing: border-box; margin: 0; padding: 0; }

  html, body {
    width: 1200px;
    height: 900px;
    overflow: hidden;
  }

  body {
    position: relative;
    background: var(--page-bg);
    font-family: "Raleway", sans-serif;
  }

  .card {
    position: absolute;
    left: 332px;
    width: 594px;
    height: 346px;
    border-radius: 18px;
    background: var(--card-bg);
  }

  .card--front { top: 82px; }
  .card--back  { top: 472px; }

  .portrait {
    position: absolute;
    border-radius: 8px;
    background: linear-gradient(180deg, var(--portrait-top) 0%, var(--portrait-bottom) 100%);
  }

  .card--front .portrait {
    left: 46px;
    top: 80px;
    width: 94px;
    height: 240px;
  }

  .card--back .portrait {
    left: 244px;
    top: 40px;
    width: 106px;
    height: 268px;
  }

  .identity {
    position: absolute;
    left: 311px;
    top: 142px;
  }

  .identity__name {
    font-size: 32px;
    font-weight: 400;
    line-height: 1;
    letter-spacing: 0.2px;
    white-space: nowrap;
  }

  .identity__first { color: var(--name-first); }
  .identity__last  { color: var(--name-last); font-weight: 300; }

  .identity__title {
    margin-top: 5px;
    margin-left: 2px;
    font-size: 15px;
    font-weight: 400;
    color: var(--title-accent);
  }

  .contact {
    position: absolute;
    left: 338px;
    top: 208px;
    list-style: none;
    font-size: 15px;
    line-height: 21px;
    color: var(--contact-text);
    white-space: nowrap;
  }
</style>
</head>
<body>
  <section class="card card--front">
    <div class="portrait" role="img" aria-label="Cartoon caricature of the cardholder in a dark suit holding papers"></div>

    <div class="identity">
      <h1 class="identity__name">
        <span class="identity__first">Daniel</span>
        <span class="identity__last">Whitacre</span>
      </h1>
      <p class="identity__title">Managing Director</p>
    </div>

    <ul class="contact">
      <li class="contact__email">DanielMWhitacre@Pelmora.com</li>
      <li class="contact__phone">(555) 218-9034</li>
      <li class="contact__web">Brenvola.net/in/DanielMWhitacre</li>
      <li class="contact__city">Houston, TX</li>
    </ul>
  </section>

  <section class="card card--back">
    <div class="portrait" role="img" aria-label="Cartoon caricature of the cardholder in a dark suit holding papers"></div>
  </section>
</body>
</html>
```